Physiotherapy Referral Pad

-Need a referral pad for physiotherapy to be provided to doctors' offices. I would like it to be simple, not too cluttered and sharp looking so doctors can quickly complete it for clients.

-I have attached my logo which I would like to include. I have also included my business cards to keep the style, font, colors etc consistent.

-I would like to include my slogan
From Our Home To Yours

-I would like it to include services options with tick boxes for Mobile, Clinic, Telehealth, NRPDLA

-I would like for it to say Call to Book or Book Online

-I would like it to include my clinic address:
472 Marrow Crescent
Whitehorse, YT
Y2B3K9

-I would like it to include my contact info:
Glen Ostrow BSc(kin), MPT, CAFCI, IMS
(867)555-0142
physio@ostrowtherapy.ca

-I would like lines for the following:
Patient Name:
Diagnosis/Recommendations:
(extra lines to fill out patient info)

Physician Signature
Date

Target Market(s)

Physicians to refer clients to physiotherapy

Industry/Entity Type

Physical Therapy

Requirements
Must have
• Clean, concise, easy to look at and find pertinant categories for physicians
Nice to have
• Ostrow Therapy color scheme. Please see business cards and website as needed
Should not have
• Not too cluttered or wordy

```html
<!DOCTYPE html>
<html lang="en">
<head>
<meta charset="utf-8">
<title>Ostrow Therapy – Referral Pad</title>
<link rel="stylesheet" href="https://fonts.googleapis.com/css2?family=Cinzel:wght@700;800&family=Montserrat:wght@400&display=swap">
<style>
  :root {
    --navy: #1b2e8a;
    --green: #0e4a2b;
    --band: #132a86;
    --paper: #f7f7f9;
    --backdrop: #e6e6e8;
    --rule: #6a6a6e;
    --ink: #3a3a3e;
    --serif: "Cinzel", "Times New Roman", serif;
    --sans: "Montserrat", Arial, sans-serif;
  }
  * { box-sizing: border-box; margin: 0; padding: 0; }
  html, body { width: 1086px; height: 1200px; overflow: hidden; background: var(--backdrop); }
  .pad {
    position: absolute; left: 137px; top: 20px;
    width: 811px; height: 1160px;
    background: var(--paper);
    box-shadow: 0 2px 10px rgba(0,0,0,.12);
    font-family: var(--serif);
    font-weight: 700;
  }
  .pad > * { position: absolute; line-height: 1; }
  .brand { left: 68px; top: 140px; display: flex; align-items: center; gap: 10px;
           color: var(--green); font-size: 22px; font-weight: 700; white-space: nowrap; }
  .brand-mark { width: 14px; height: 14px; background: var(--green); flex: none; }
  .contact { left: 530px; top: 88px; font-family: var(--sans); font-weight: 400; font-size: 15px; color: var(--ink); line-height: 18px; font-style: normal; }
  .contact p { white-space: nowrap; }
  .contact .gap { margin-top: 8px; }
  .contact .item { display: flex; align-items: center; gap: 4px; margin-bottom: 4px; }
  .contact svg { width: 15px; height: 15px; flex: none; }
  .practitioner { left: 0; width: 100%; text-align: center; font-weight: 700; }
  .practitioner-name { top: 345px; font-size: 40px; color: var(--green); }
  .credentials { top: 391px; font-size: 18px; color: var(--navy); }
  .services { top: 436px; left: 0; width: 100%; display: flex; justify-content: center; gap: 12px;
              font-size: 21px; color: var(--navy); white-space: nowrap; }
  .service { display: flex; align-items: center; gap: 8px; }
  .tickbox { width: 18px; height: 18px; border: 2px solid var(--green); display: inline-block; }
  .field { display: flex; align-items: flex-end; gap: 12px; }
  .label { font-size: 20px; color: var(--navy); white-space: nowrap; line-height: 1; }
  .field .rule { flex: 1; margin-bottom: 2px; }
  .rule { height: 1.5px; background: var(--rule); }
  .cta { left: 0; width: 100%; text-align: center; top: 1071px; font-size: 22px; letter-spacing: 3px; color: var(--green); }
  .slogan-band { left: 0; top: 1111px; width: 100%; height: 49px; background: var(--band); color: #fff;
                 display: flex; align-items: center; justify-content: center; font-size: 20px; letter-spacing: 5px; }
</style>
</head>
<body>
<main class="pad">
  <div class="brand">
    <span class="brand-mark"></span>
    <span class="brand-name">Ostrow Therapy</span>
  </div>

  <address class="contact">
    <p>472 Marrow Crescent</p>
    <p>Whitehorse, YT Y2B3K9</p>
    <div class="gap"></div>
    <p class="item"><svg viewBox="0 0 16 16"><circle cx="8" cy="8" r="8" fill="#0e4a2b"/><path d="M5 4.5l1.5-.5 1 2-1 .8a5 5 0 0 0 2.7 2.7l.8-1 2 1-.5 1.5c-3.5.3-6.8-3-6.5-6.5z" fill="#fff"/></svg>(867)555-0142</p>
    <p class="item"><svg viewBox="0 0 16 16"><circle cx="8" cy="8" r="8" fill="#0e4a2b"/><rect x="4" y="5" width="8" height="6" fill="none" stroke="#fff" stroke-width="1.2"/><path d="M4 5l4 3.2L12 5" fill="none" stroke="#fff" stroke-width="1.2"/></svg>physio@ostrowtherapy.ca</p>
    <p class="item"><svg viewBox="0 0 16 16"><circle cx="8" cy="8" r="8" fill="#0e4a2b"/><circle cx="8" cy="8" r="4" fill="none" stroke="#fff" stroke-width="1.2"/><path d="M4 8h8M8 4c-2 2.4-2 5.6 0 8M8 4c2 2.4 2 5.6 0 8" fill="none" stroke="#fff" stroke-width="1"/></svg>www.ostrowtherapy.ca</p>
  </address>

  <h1 class="practitioner practitioner-name">GLEN OSTROW</h1>
  <p class="practitioner credentials">BSc(kin), MPT, CAFCI, IMS</p>

  <div class="services">
    <span class="service"><span class="tickbox"></span>MOBILE</span>
    <span class="service"><span class="tickbox"></span>CLINIC</span>
    <span class="service"><span class="tickbox"></span>TELEHEALTH</span>
    <span class="service"><span class="tickbox"></span>NRPDLA</span>
  </div>

  <div class="field" style="left:83px;top:518px;width:645px">
    <span class="label">PATIENT NAME:</span><span class="rule"></span>
  </div>
  <div class="rule" style="left:83px;top:605px;width:645px"></div>

  <div class="field" style="left:83px;top:655px;width:645px">
    <span class="label">Diagnosis/Recommendations:</span><span class="rule"></span>
  </div>
  <div class="rule" style="left:83px;top:742px;width:645px"></div>
  <div class="rule" style="left:87px;top:810px;width:646px"></div>

  <div class="field" style="left:85px;top:901px;width:645px">
    <span class="label">Physician Signature</span><span class="rule"></span>
  </div>

  <div class="field" style="left:85px;top:970px;width:645px">
    <span class="label">Date</span><span class="rule"></span>
  </div>

  <p class="cta">Call to Book or Book Online</p>
  <footer class="slogan-band">FROM OUR HOME TO YOURS</footer>
</main>
</body>
</html>
```